New Innovative Counselling and psychotherapy Service needs Business Card design

Keep it simple and professional. On one side, just company name and logo (perhaps in all blue) and maybe a tag line.

On other side (all white) my name and Qualifications in centre

Industry/Entity Type

Health And Wellness

Contact Information for Business Card

Dara Whelby
Counsellor & Psychotherapist
BSc (Psychol.), BA, Dip. (Couns. & Psych.), PG.Cert (CBT), FGTrK, ONRE

I will also require Mobile no, Email and web site address of which I'll pass on to final designer.

Font styles to use
Sans Serif

Requirements
Must have
• My Logo Only and please use the colours in logo that is in it.
Should not have
• Any other images

```html
<!DOCTYPE html>
<html lang="en">
<head>
<meta charset="utf-8">
<title>Thrive Lane – Business Card</title>
<link href="https://fonts.googleapis.com/css2?family=Roboto:wght@400;700&display=swap" rel="stylesheet">
<style>
  :root {
    --canvas: #e8e8e8;
    --card-white: #f6f6f6;
    --blue: #3d9ad6;
    --blue-light: #4db0e2;
    --sky: #62bfe8;
    --mint: #8fd0b0;
    --green: #9bd572;
    --leaf: #7cc243;
    --ink: #3a3a3a;
    --ink-soft: #555555;
  }
  * { margin: 0; padding: 0; box-sizing: border-box; }
  html, body { width: 1200px; height: 726px; overflow: hidden; }
  body {
    background: var(--canvas);
    font-family: 'Roboto', Arial, sans-serif;
    position: relative;
  }
  .card {
    position: absolute;
    top: 220px;
    width: 500px;
    height: 286px;
    border-radius: 3px;
    box-shadow: 0 6px 18px rgba(0,0,0,0.12);
    overflow: hidden;
  }
  /* Front */
  .card-front {
    left: 70px;
    background: linear-gradient(110deg, var(--sky) 0%, var(--mint) 50%, var(--green) 100%);
    display: flex;
    align-items: center;
    justify-content: center;
  }
  .front-wordmark {
    color: #ffffff;
    font-size: 46px;
    font-weight: 400;
    letter-spacing: 1px;
  }
  /* Back */
  .card-back {
    left: 630px;
    background: var(--card-white);
  }
  .side-band {
    position: absolute;
    left: 0; top: 0; bottom: 0;
    width: 58px;
    background: linear-gradient(180deg, var(--blue-light), var(--blue));
    border-right: 4px solid var(--leaf);
  }
  .brand {
    position: absolute;
    left: 80px;
    top: 36px;
    display: flex;
    align-items: center;
    gap: 14px;
  }
  .brand-dot {
    width: 42px; height: 42px;
    border-radius: 50%;
    background: var(--blue);
  }
  .brand-name {
    font-size: 32px;
    font-weight: 400;
    color: var(--ink);
    letter-spacing: 0.5px;
  }
  .person {
    position: absolute;
    left: 80px;
    top: 104px;
  }
  .person-name {
    font-size: 21px;
    font-weight: 700;
    color: var(--blue);
    margin-bottom: 3px;
  }
  .person-role, .person-quals {
    font-size: 12px;
    line-height: 15px;
    color: var(--ink-soft);
  }
  .contacts {
    position: absolute;
    left: 80px;
    top: 196px;
    list-style: none;
  }
  .contacts li {
    display: flex;
    align-items: center;
    gap: 12px;
    font-size: 13.5px;
    line-height: 19px;
    color: var(--ink);
  }
  .contacts svg { width: 13px; height: 13px; flex: none; }
</style>
</head>
<body>
  <section class="card card-front">
    <span class="front-wordmark">Thrive Lane</span>
  </section>

  <section class="card card-back">
    <div class="side-band"></div>

    <div class="brand">
      <span class="brand-dot"></span>
      <span class="brand-name">Thrive Lane</span>
    </div>

    <div class="person">
      <h1 class="person-name">Dara Whelby</h1>
      <p class="person-role">Counsellor &amp; Psychotherapist</p>
      <p class="person-quals">BSc (Psychol.), BA, Dip. (Couns. &amp; Psych.),<br>PG.Cert (CBT), FGTrK, ONRE</p>
    </div>

    <ul class="contacts">
      <li>
        <svg viewBox="0 0 14 14" aria-hidden="true"><path d="M2 4c0-1 1-2 2-2h6c1 0 2 1 2 2v1H9V4H5v1H2z M3 6h8l1 6H2z" fill="#3d9ad6"/></svg>
        0123 456 7890
      </li>
      <li>
        <svg viewBox="0 0 14 14" aria-hidden="true"><rect x="1" y="3" width="12" height="8" fill="#7cc243"/><path d="M1 3l6 5 6-5" stroke="#fff" stroke-width="1.2" fill="none"/></svg>
        dara.w@ThriveLane.com
      </li>
      <li>
        <svg viewBox="0 0 14 14" aria-hidden="true"><circle cx="7" cy="7" r="6" fill="#7cc243"/><path d="M1 7h12M7 1c-3 3-3 9 0 12M7 1c3 3 3 9 0 12" stroke="#fff" stroke-width="0.9" fill="none"/></svg>
        www.ThriveLane.com
      </li>
    </ul>
  </section>
</body>
</html>
```